US-based arts and education non-profit needs logo and signage for South African affiliate

We need a logo and sign for the "Scrap to Splendor" (STS) recycling program, based out of a local community center in Port Elizabeth, South Africa. The community center also houses a community garden and afterschool program. The sign should be 5' x 4'. Title: Scrap to Splendor (with logo). Subtitle 1: "Our Shared Lantern". Subtitle 2: "in partnership with Lantern Nine" (with Lantern Nine logo). We would like to see designs that are vibrant and welcoming. The final design should communicate joy and community.

```html
<!DOCTYPE html>
<html lang="en">
<head>
<meta charset="utf-8">
<title>Scrap to Splendor – Our Shared Lantern sign</title>
<link rel="stylesheet" href="https://fonts.googleapis.com/css2?family=Montserrat:wght@300;500;600;800&display=swap">
<style>
  :root {
    --page-bg: #ececec;
    --sign-bg-top: #f4f4f4;
    --sign-bg-bottom: #ededed;
    --leaf-green: #5b9340;
    --badge-green: #1f7a37;
    --earth-brown: #46321a;
    --partner-purple: #6a3396;
    --dash-grey: #8a8a8a;
    --tone-tree: #5f9e48;
    --tone-sun: #f6c338;
    --tone-orange: #f08a2c;
    --tone-violet: #4d3d9a;
    --tone-sky: #2f9fd0;
    --tone-blue: #4a6cc0;
    --tone-teal: #3a9a9c;
    --tone-ground: #2f7a5c;
  }
  * { box-sizing: border-box; margin: 0; padding: 0; }
  html, body {
    width: 800px;
    height: 1200px;
    overflow: hidden;
    background: var(--page-bg);
    font-family: "Montserrat", Arial, sans-serif;
  }
  .sign {
    position: absolute;
    left: 40px;
    top: 312px;
    width: 720px;
    height: 576px;
    background: linear-gradient(180deg, var(--sign-bg-top), var(--sign-bg-bottom));
    box-shadow: 0 6px 24px rgba(0,0,0,0.18);
    overflow: hidden;
  }
  .program-mark {
    position: absolute;
    top: 52px;
    left: 0;
    width: 100%;
    display: flex;
    justify-content: center;
    align-items: center;
    gap: 12px;
  }
  .program-mark__dot {
    width: 46px;
    height: 46px;
    border-radius: 50%;
    background: var(--leaf-green);
  }
  .program-mark__name {
    font-weight: 800;
    font-size: 40px;
    line-height: 50px;
    color: var(--leaf-green);
    letter-spacing: 1px;
  }
  .program-title {
    position: absolute;
    top: 142px;
    width: 100%;
    text-align: center;
    font-weight: 300;
    font-size: 33px;
    line-height: 40px;
    color: var(--leaf-green);
    letter-spacing: 0.5px;
  }
  .headline {
    position: absolute;
    top: 0;
    left: 0;
    width: 100%;
    font-weight: 800;
  }
  .headline__lead,
  .headline__main {
    position: absolute;
    left: 0;
    width: 100%;
    text-align: center;
  }
  .headline__lead {
    top: 189px;
    font-size: 58px;
    line-height: 58px;
    color: var(--leaf-green);
    letter-spacing: -1px;
  }
  .headline__main {
    top: 236px;
    font-size: 96px;
    line-height: 96px;
    color: var(--earth-brown);
    letter-spacing: -2px;
  }
  .divider {
    position: absolute;
    top: 334px;
    left: 70px;
    width: 578px;
    border-top: 2px dashed var(--dash-grey);
  }
  .partnership {
    position: absolute;
    top: 350px;
    left: 211px;
    display: flex;
    align-items: center;
    gap: 8px;
    z-index: 1;
  }
  .partnership__badge {
    width: 140px;
    height: 33px;
    border-radius: 5px;
    background: var(--badge-green);
    color: #fff;
    font-weight: 500;
    font-size: 11px;
    line-height: 13px;
    display: flex;
    flex-direction: column;
    justify-content: center;
    padding-left: 28px;
  }
  .partnership__rule {
    width: 1.5px;
    height: 26px;
    background: var(--dash-grey);
  }
  .partner-mark {
    display: flex;
    align-items: center;
    gap: 7px;
  }
  .partner-mark__dot {
    width: 34px;
    height: 34px;
    border-radius: 50%;
    background: var(--partner-purple);
  }
  .partner-mark__name {
    font-weight: 600;
    font-size: 13px;
    color: var(--partner-purple);
    letter-spacing: 0.3px;
  }
  .community-scene {
    position: absolute;
    left: 0;
    bottom: 0;
    width: 720px;
    height: 190px;
  }
</style>
</head>
<body>
  <main class="sign">
    <div class="program-mark">
      <span class="program-mark__dot"></span>
      <span class="program-mark__name">STS</span>
    </div>

    <p class="program-title">SCRAP TO SPLENDOR</p>

    <h1 class="headline">
      <span class="headline__lead">OUR SHARED</span>
      <span class="headline__main">LANTERN</span>
    </h1>

    <div class="divider"></div>

    <div class="partnership">
      <div class="partnership__badge">
        <span>In partnership</span>
        <span>with Lantern Nine</span>
      </div>
      <span class="partnership__rule"></span>
      <div class="partner-mark">
        <span class="partner-mark__dot"></span>
        <span class="partner-mark__name">LANTERN NINE</span>
      </div>
    </div>

    <svg class="community-scene" viewBox="0 0 720 190" preserveAspectRatio="none" role="img"
         aria-label="Colourful illustration of smiling volunteers collecting litter in a park: a woman with a litter picker, a girl gathering leaves, a kneeling man filling a bag, a young man pushing a blue recycling cart, and a woman dropping a bag into yellow and teal recycling bins, among trees and bushes on green grass">
      <defs>
        <linearGradient id="sceneTones" x1="0" y1="0" x2="1" y2="0">
          <stop offset="0" stop-color="var(--tone-tree)"/>
          <stop offset="0.16" stop-color="var(--tone-sun)"/>
          <stop offset="0.32" stop-color="var(--tone-orange)"/>
          <stop offset="0.46" stop-color="var(--tone-sky)"/>
          <stop offset="0.6" stop-color="var(--tone-violet)"/>
          <stop offset="0.72" stop-color="var(--tone-blue)"/>
          <stop offset="0.84" stop-color="var(--tone-sun)"/>
          <stop offset="0.94" stop-color="var(--tone-teal)"/>
          <stop offset="1" stop-color="var(--tone-ground)"/>
        </linearGradient>
      </defs>
      <rect x="0" y="0" width="720" height="190" fill="url(#sceneTones)"/>
    </svg>
  </main>
</body>
</html>
```